Moravel Aesthetic Doctor

I require an elegant, luxurious looking business card for my aesthetic business. I am a doctor and that will set me aside from competitors. I am planning to provide home and spa based treatments to clients with high expectations. I have attached my logo.

```html
<!DOCTYPE html>
<html lang="en">
<head>
<meta charset="utf-8">
<title>Moravel Aesthetic Doctor – Business Card</title>
<link rel="stylesheet" href="https://fonts.googleapis.com/css2?family=Lato:wght@400&family=Montserrat:wght@400;500&display=swap">
<style>
  :root {
    --backdrop: #e4e4e4;
    --card: #ffffff;
    --ink: #333335;
    --ink-soft: #6d6e70;
    --brand-grey: #8a8c8f;
    --brand-blue: #2f9fdc;
    --blue-light: #a9dcf3;
    --blue-mid: #4fb3e6;
    --blue-deep: #1f6fbf;
  }
  * { box-sizing: border-box; margin: 0; padding: 0; }
  html, body { width: 1200px; height: 896px; overflow: hidden; }
  body {
    background: var(--backdrop);
    font-family: "Montserrat", sans-serif;
    color: var(--ink);
    position: relative;
  }
  .card {
    position: absolute;
    left: 302px;
    width: 619px;
    height: 354px;
    background: var(--card);
    box-shadow: 0 3px 8px rgba(0,0,0,0.22);
  }
  .card--front { top: 94px; }
  .card--back  { top: 469px; }

  /* Front */
  .brand {
    position: absolute;
    left: 130px;
    top: 76px;
    display: flex;
    align-items: center;
    gap: 16px;
  }
  .brand__dot {
    width: 96px;
    height: 96px;
    border-radius: 50%;
    background: var(--blue-light);
    flex: none;
  }
  .brand__name {
    font-family: "Montserrat", sans-serif;
    font-weight: 400;
    color: var(--brand-grey);
    line-height: 1.05;
    text-transform: uppercase;
  }
  .brand__name-main { display: block; font-size: 44px; letter-spacing: 1px; }
  .brand__name-sub  { display: block; font-size: 19px; letter-spacing: 1.5px; margin-top: 4px; }
  .tagline {
    position: absolute;
    left: 273px;
    top: 168px;
    font-family: "Lato", sans-serif;
    font-size: 13.5px;
    color: var(--ink-soft);
  }
  .services {
    position: absolute;
    left: 0;
    right: 0;
    top: 282px;
    text-align: center;
    font-size: 14.5px;
    line-height: 18px;
    color: var(--ink);
  }

  /* Back */
  .mark-art {
    position: absolute;
    left: 300px;
    top: 30px;
    width: 296px;
    height: 226px;
    border-radius: 50% 46% 44% 56% / 40% 48% 52% 60%;
    background: radial-gradient(ellipse at 65% 50%, var(--blue-mid) 0%, var(--blue-light) 60%, rgba(169,220,243,0) 100%);
  }
  .person {
    position: absolute;
    left: 33px;
    top: 193px;
  }
  .person__name {
    font-size: 19px;
    font-weight: 400;
    color: var(--ink);
  }
  .person__cred {
    font-size: 9.5px;
    color: var(--brand-blue);
    margin-left: 3px;
    letter-spacing: 0.3px;
  }
  .person__diploma {
    margin-top: 5px;
    font-size: 14.5px;
    line-height: 18px;
    color: var(--brand-blue);
  }
  .contacts {
    position: absolute;
    left: 33px;
    top: 267px;
    list-style: none;
    font-size: 14.5px;
    line-height: 19px;
    color: var(--ink);
  }
  .contacts li { display: flex; align-items: center; gap: 7px; }
  .contacts svg { width: 12px; height: 12px; fill: var(--brand-blue); flex: none; }
  .social { display: inline-flex; gap: 8px; margin-left: 22px; }
  .social span {
    width: 11px; height: 11px; border-radius: 50%;
    background: var(--brand-blue);
  }
</style>
</head>
<body>
  <section class="card card--front" aria-label="Business card front">
    <div class="brand">
      <div class="brand__dot"></div>
      <div class="brand__name">
        <span class="brand__name-main">Moravel</span>
        <span class="brand__name-sub">Aesthetic Doctor</span>
      </div>
    </div>
    <p class="tagline">Home and Spa Based Treatments</p>
    <p class="services">Dermal injectables - Plasma facials - Microneedling<br>Skin boosters - Excessive sweating</p>
  </section>

  <section class="card card--back" aria-label="Business card back">
    <div class="mark-art" role="img" aria-label="Large brand emblem in layered blue tones"></div>
    <div class="person">
      <p class="person__name">Dr Elise Varnum<span class="person__cred">MRCPCH MD</span></p>
      <p class="person__diploma">Australasian Diploma<br>of Aesthetic Medicine</p>
    </div>
    <ul class="contacts">
      <li>
        <svg viewBox="0 0 24 24" aria-hidden="true"><path d="M6.6 10.8a15.2 15.2 0 0 0 6.6 6.6l2.2-2.2c.3-.3.7-.4 1-.2 1.1.4 2.3.6 3.6.6.6 0 1 .4 1 1V20c0 .6-.4 1-1 1A17 17 0 0 1 3 4c0-.6.4-1 1-1h3.5c.6 0 1 .4 1 1 0 1.3.2 2.5.6 3.6.1.3 0 .7-.2 1z"/></svg>
        0800 555 318
      </li>
      <li>
        <svg viewBox="0 0 24 24" aria-hidden="true"><path d="M2 5h20v14H2z" fill="none"/><path d="M2 5h20v2l-10 6L2 7zM2 9l10 6 10-6v10H2z"/></svg>
        elise@moravel.co.nz
      </li>
      <li>
        <svg viewBox="0 0 24 24" aria-hidden="true"><path d="M12 2a10 10 0 1 0 0 20 10 10 0 0 0 0-20zm0 2c.9 1.2 1.6 2.8 1.9 5h-3.8c.3-2.2 1-3.8 1.9-5zM4.3 9h3.8a17 17 0 0 0 0 6H4.3a8 8 0 0 1 0-6zm5.8 0h3.8a15 15 0 0 1 0 6h-3.8a15 15 0 0 1 0-6zm5.8 0h3.8a8 8 0 0 1 0 6h-3.8a17 17 0 0 0 0-6zM12 20c-.9-1.2-1.6-2.8-1.9-5h3.8c-.3 2.2-1 3.8-1.9 5z"/></svg>
        www.moravel.co.nz
        <span class="social" aria-label="Social links"><span></span><span></span></span>
      </li>
    </ul>
  </section>
</body>
</html>
```